Business Card - high end, modern health care

Hey designers!

We need a double sided business card for the boutique, cutting edge physical therapy rehabilitation centre in Sydney's Northern Beaches.

With the most qualified physios in the area The Harbourview Motion Clinic does what other physiotherapy practices do not, we take our time with our patients giving them longer appointments, better physios and therefor faster results!

We guarantee that the service people receive at THMC will be unparalleled.

Hence we need a business card to reflect our modern, boutique, high end service. The final design needs to reflect that we are in a class of our own yet with the feel of beachside retreat.

Below I have attached our logo in both blue on white and white on blue. The exact colour is;
and the font that we have used in our logo is Tex Gyre Aventador.

I like the idea of the blue as the main colour as it is more eye catching and our signage onto the main road will be in this blue and in the interest of consistency across marketing the blue needs to be a part of the design. However I would appreciate a few designs onto a wooden background as this is a visual theme within the fitout of the practice.

The design needs to be of standard size (91x55mm).

Target Market(s)

We target people who have an end outcome in mind and those who have had poor experiences with other providers and ensure that everyone gets the care that they deserve with a premium service that is tailored to the individuals circumstances. As a premium service, the target market is highly educated, business and tech savvy with the additional target market of elderly people who have self funded their retirement and see value in paying for the best ongoing rehabilitation to maintain independence.

Industry/Entity Type

Physical Therapy

Contact Information for Business Card

Name, designation( Titled Musculoskeletal Physiotherapist... there will also be those in the company that have multiple designations ie 5 or 6 words long), phone number, email, facebook, instagram, address

Font styles to use
Sans Serif

Colors

Designer to choose colors to be used in the design.

Requirements
Must have
• Front - The logo as large as possible, blue or wooden theme, and all of the important details.
• Back - A blank space/lines on which to write appointment times (no "Appointment, date, time" etc.)
Nice to have
• facebook url
• logos for facebook and instagram
• Mini logos for the phone and email?

```html
<!DOCTYPE html>
<html lang="en">
<head>
<meta charset="utf-8">
<title>The Harbourview Motion Clinic – Business Card</title>
<link href="https://fonts.googleapis.com/css2?family=Montserrat:wght@400;600&display=swap" rel="stylesheet">
<style>
  :root {
    --backdrop: #1c1f33;
    --brand-blue: #0f59a8;
    --card-white: #ffffff;
    --ink: #222222;
    --ink-soft: #555555;
    --rule: #6b6b6b;
    --dash: #bdbdbd;
    --accent-pink: #e0457b;
  }
  * { margin: 0; padding: 0; box-sizing: border-box; }
  html, body { width: 1200px; height: 1200px; overflow: hidden; }
  body {
    background: var(--backdrop);
    font-family: "Montserrat", sans-serif;
    position: relative;
  }
  .card {
    position: absolute;
    left: 170px;
    width: 860px;
    height: 520px;
    border-radius: 44px;
    overflow: hidden;
  }
  .card--front { top: 50px; background: var(--brand-blue); }
  .card--back { top: 630px; background: var(--card-white); color: var(--ink); }

  /* Front */
  .front-mark {
    position: absolute;
    left: 50%; top: 120px;
    transform: translateX(-50%);
    width: 170px; height: 170px;
    border: 14px solid var(--card-white);
    border-radius: 50%;
  }
  .front-name {
    position: absolute;
    left: 0; right: 0; top: 320px;
    text-align: center;
    color: var(--card-white);
    font-weight: 600;
    font-size: 34px;
    letter-spacing: 1px;
    line-height: 1.25;
    text-transform: uppercase;
  }

  /* Back */
  .brand {
    position: absolute;
    right: 60px; top: 56px;
    display: flex; align-items: center; gap: 16px;
  }
  .brand__dot {
    width: 50px; height: 50px; border-radius: 50%;
    background: var(--brand-blue);
  }
  .brand__name {
    color: var(--brand-blue);
    font-weight: 600;
    font-size: 22px;
    line-height: 1.2;
    text-transform: uppercase;
    letter-spacing: 0.5px;
  }
  .rule { position: absolute; height: 1.5px; background: var(--rule); }
  .rule--top { left: 380px; right: 60px; top: 140px; }
  .rule--mid { left: 60px; right: 440px; top: 300px; }
  .rule--low { left: 60px; right: 60px; top: 440px; }
  .rule--dash {
    left: 60px; right: 60px; top: 480px;
    height: 0; background: none;
    border-top: 2px dashed var(--dash);
  }
  .person { position: absolute; left: 60px; top: 205px; }
  .person__name { font-size: 38px; font-weight: 400; }
  .person__name span { color: var(--brand-blue); }
  .person__role { font-size: 18px; color: var(--ink-soft); margin-top: 4px; }
  .social { position: absolute; left: 520px; top: 170px; }
  .contact { position: absolute; left: 60px; top: 330px; }
  .line-item {
    display: flex; align-items: center; gap: 14px;
    font-size: 20px; margin-bottom: 14px;
  }
  .social .line-item { font-size: 18px; margin-bottom: 12px; }
  .social-dot { width: 26px; height: 26px; border-radius: 50%; }
  .social-dot--fb { background: var(--brand-blue); }
  .social-dot--ig { background: var(--accent-pink); }
  .icon { width: 28px; height: 28px; }
</style>
</head>
<body>
  <section class="card card--front" aria-label="Card front">
    <div class="front-mark"></div>
    <div class="front-name">The Harbourview<br>Motion Clinic</div>
  </section>

  <section class="card card--back" aria-label="Card back">
    <div class="brand">
      <div class="brand__dot"></div>
      <div class="brand__name">The Harbourview<br>Motion Clinic</div>
    </div>
    <div class="rule rule--top"></div>

    <div class="person">
      <div class="person__name">Name of <span>Person</span></div>
      <div class="person__role">Designation</div>
    </div>

    <div class="social">
      <div class="line-item"><span class="social-dot social-dot--fb"></span>facebook/name</div>
      <div class="line-item"><span class="social-dot social-dot--ig"></span>instagram_name</div>
    </div>

    <div class="rule rule--mid"></div>

    <div class="contact">
      <div class="line-item">
        <svg class="icon" viewBox="0 0 28 28" aria-hidden="true">
          <circle cx="14" cy="14" r="12" fill="none" stroke="#222" stroke-width="2"/>
          <path d="M10 8c-1 1-1 3 1 6s4 5 6 5c1 0 2-1 2-2l-2-2-2 1c-1-1-2-2-3-4l1-2-2-2z" fill="#222"/>
        </svg>
        555.014.2870
      </div>
      <div class="line-item">
        <svg class="icon" viewBox="0 0 28 28" aria-hidden="true">
          <rect x="3" y="7" width="22" height="15" fill="none" stroke="#222" stroke-width="2"/>
          <path d="M3 7l11 9 11-9" fill="none" stroke="#222" stroke-width="2"/>
        </svg>
        hello@harbourviewmotion.com
      </div>
    </div>

    <div class="rule rule--low"></div>
    <div class="rule rule--dash"></div>
  </section>
</body>
</html>
```